Business Card Design

We need a business card designed for our new company. Prefer a black card with white logo & writing.

Contact Information for Business Card

Ted Galloway, address: 7-4812 Fernhollow Road, Abbotsford, BC, V3K 8R2, Office Phone: 604-712-3390, Cell: 604-947-2164, Email: ted@resinworkshub.ca

Colors

Designer to choose only greyscale colors for use in the design.

```html
<!DOCTYPE html>
<html lang="en">
<head>
<meta charset="UTF-8">
<title>Resinworks Hub – Business Card</title>
<link href="https://fonts.googleapis.com/css2?family=Poppins:wght@300;400;600;700;800&display=swap" rel="stylesheet">
<style>
  :root {
    --bg: #232325;
    --card-grey: #222226;
    --card-black: #050505;
    --white: #ffffff;
    --rule: #d9d9d9;
  }
  * { margin: 0; padding: 0; box-sizing: border-box; }
  html, body { width: 1200px; height: 711px; overflow: hidden; }
  body {
    background: var(--bg);
    font-family: "Poppins", sans-serif;
    color: var(--white);
    position: relative;
  }
  .card {
    position: absolute;
    top: 201px;
    width: 540px;
    height: 309px;
    border-radius: 10px;
    overflow: hidden;
    background: var(--card-grey);
    box-shadow: 0 14px 30px rgba(0,0,0,0.55);
  }
  .card--front { left: 30px; }
  .card--back { left: 630px; }
  .band {
    position: absolute;
    left: 0; right: 0; bottom: 0;
    background: var(--card-black);
    border-top: 2px solid var(--rule);
  }
  .card--front .band { height: 96px; }
  .card--back .band { height: 150px; }
  .wordmark {
    position: absolute;
    font-weight: 700;
    letter-spacing: 1px;
    white-space: nowrap;
    color: var(--white);
  }
  .card--front .wordmark {
    left: 0; right: 0; top: 82px;
    text-align: center;
    font-size: 34px;
  }
  .card--back .wordmark {
    left: 34px; top: 64px;
    font-size: 24px;
  }
  .website-front {
    position: absolute;
    left: 0; right: 0; top: 20px;
    text-align: center;
    font-size: 13px;
    font-weight: 400;
    letter-spacing: 0.5px;
  }
  .person {
    position: absolute;
    right: 30px; top: 44px;
    text-align: right;
  }
  .person__name { font-size: 27px; line-height: 1.1; }
  .person__first { font-weight: 800; }
  .person__last { font-weight: 300; }
  .person__role { font-size: 12px; font-weight: 600; margin-top: 2px; }
  .contacts {
    position: absolute;
    right: 26px; top: 14px;
    list-style: none;
  }
  .contacts li {
    display: flex;
    justify-content: flex-end;
    align-items: center;
    gap: 8px;
    font-size: 13px;
    line-height: 24px;
    font-weight: 400;
  }
  .contacts svg { width: 13px; height: 13px; flex: none; }
  .address {
    position: absolute;
    left: 30px; bottom: 22px;
    display: flex;
    align-items: center;
    gap: 12px;
    font-size: 13px;
    line-height: 19px;
  }
  .address svg { width: 16px; height: 20px; flex: none; }
</style>
</head>
<body>

<section class="card card--front" aria-label="Card front">
  <div class="wordmark">RESINWORKS HUB</div>
  <div class="band">
    <p class="website-front">www.resinworkshub.ca</p>
  </div>
</section>

<section class="card card--back" aria-label="Card back">
  <div class="wordmark">RESINWORKS HUB</div>
  <div class="person">
    <div class="person__name"><span class="person__first">Ted</span> <span class="person__last">Galloway</span></div>
    <div class="person__role">Owner</div>
  </div>
  <div class="band">
    <ul class="contacts">
      <li>604-712-3390
        <svg viewBox="0 0 24 24" fill="none" stroke="#fff" stroke-width="2.2"><path d="M5 3h4l2 5-3 2a12 12 0 0 0 6 6l2-3 5 2v4a2 2 0 0 1-2 2A18 18 0 0 1 3 5a2 2 0 0 1 2-2z"/></svg>
      </li>
      <li>604-947-2164
        <svg viewBox="0 0 24 24" fill="none" stroke="#fff" stroke-width="2.2"><rect x="6" y="2" width="12" height="20" rx="2"/><line x1="11" y1="18" x2="13" y2="18"/></svg>
      </li>
      <li>www.resinworkshub.ca
        <svg viewBox="0 0 24 24" fill="none" stroke="#fff" stroke-width="2"><circle cx="12" cy="12" r="10"/><ellipse cx="12" cy="12" rx="4" ry="10"/><line x1="2" y1="12" x2="22" y2="12"/></svg>
      </li>
      <li>ted@resinworkshub.ca
        <svg viewBox="0 0 24 24" fill="none" stroke="#fff" stroke-width="2"><rect x="2" y="5" width="20" height="14" rx="1"/><path d="M2 6l10 7 10-7"/></svg>
      </li>
    </ul>
    <div class="address">
      <svg viewBox="0 0 16 20" fill="none" stroke="#fff" stroke-width="1.6"><path d="M8 1a6 6 0 0 1 6 6c0 4-6 10-6 10S2 11 2 7a6 6 0 0 1 6-6z"/><circle cx="8" cy="7" r="2"/><path d="M3 18h10"/></svg>
      <p>7-4812 Fernhollow Road,<br>Abbotsford, BC, V3K 8R2.</p>
    </div>
  </div>
</section>

</body>
</html>
```